Verodex business card

Business card for sustainable investment company called "Verodex". Verodex is an exchange platform selling carbon credits between buyers and sellers. Carbon Credits are an environmental commodity for reducing global carbon emissions.

the card should obviously have our logo and the theme should be sustainability/environment mixed with a trading platform.

Contact Information for Business Card

Logo, Name, Title, Phone, Email

Colors
0054AA
0677BA
7BADD7
CADEEF
E8F1F8
0094D4
00A9DD
6FCCEA
C7EBF8
E9F6FB
00AB8E
00BBA5
67D7C9
C6EFE9
E9F9F6
59FF00
82FF00
B8FF75
E3FFCB
F4FFEA

```html
<!DOCTYPE html>
<html lang="en">
<head>
<meta charset="UTF-8">
<title>Verodex Business Card</title>
<link href="https://fonts.googleapis.com/css2?family=Montserrat:wght@400;500;600;700&display=swap" rel="stylesheet">
<style>
  :root {
    --bg: #e9edf1;
    --white: #ffffff;
    --navy: #1c2b4a;
    --deep-blue: #3f6dbf;
    --mid-blue: #2fb6e6;
    --sky: #5ccbe0;
    --accent-blue: #2fa6e0;
    --text-dark: #1e2533;
  }
  * { box-sizing: border-box; margin: 0; padding: 0; }
  html, body {
    width: 1200px; height: 900px; overflow: hidden;
    background: var(--bg);
    font-family: "Montserrat", sans-serif;
  }
  .stage { position: relative; width: 1200px; height: 900px; }
  .card {
    position: absolute; left: 260px; width: 680px; height: 388px;
    overflow: hidden; box-shadow: 0 6px 18px rgba(20, 30, 50, 0.18);
  }
  .card--front {
    top: 46px;
    background: linear-gradient(20deg, var(--sky) 0%, var(--mid-blue) 40%, #4a8fd0 70%, var(--deep-blue) 100%);
  }
  .card--back { top: 466px; background: var(--white); }

  .brand { position: absolute; display: flex; align-items: center; gap: 18px; }
  .brand__mark { width: 44px; height: 44px; }
  .brand__name { font-weight: 600; letter-spacing: 2px; line-height: 1; }

  .card--front .brand { left: 50%; top: 50%; transform: translate(-50%, -50%); }
  .card--front .brand__mark { background: var(--white); }
  .card--front .brand__name { color: var(--white); font-size: 64px; }

  .card--back .brand { left: 150px; top: 54px; }
  .card--back .brand__mark { background: var(--accent-blue); width: 40px; height: 40px; }
  .card--back .brand__name { color: var(--navy); font-size: 52px; }

  .wave { position: absolute; inset: 0; width: 680px; height: 388px; }

  .person { position: absolute; left: 150px; top: 138px; text-align: right; width: 230px; }
  .person__name { font-weight: 700; font-size: 24px; letter-spacing: 0.5px; }
  .person__first { color: var(--accent-blue); }
  .person__last { color: var(--navy); }
  .person__title { font-size: 16px; font-weight: 500; color: var(--text-dark); margin-top: 4px; }

  .divider {
    position: absolute; left: 396px; top: 130px; width: 2px; height: 84px;
    background: var(--accent-blue);
  }

  .contact { position: absolute; left: 412px; top: 130px; list-style: none; }
  .contact__item {
    display: flex; align-items: center; gap: 8px;
    font-size: 16px; font-weight: 500; color: var(--text-dark);
    height: 28px;
  }
  .contact__icon { width: 16px; height: 16px; flex: none; }
</style>
</head>
<body>
<main class="stage">
  <section class="card card--front">
    <div class="brand">
      <span class="brand__mark"></span>
      <span class="brand__name">VERODEX</span>
    </div>
  </section>

  <section class="card card--back">
    <svg class="wave" viewBox="0 0 680 388" aria-hidden="true">
      <defs>
        <linearGradient id="waveFill" x1="0" y1="1" x2="1" y2="0">
          <stop offset="0" stop-color="#5ccbe0"/>
          <stop offset="0.45" stop-color="#2fb6e6"/>
          <stop offset="1" stop-color="#3f6dbf"/>
        </linearGradient>
      </defs>
      <path d="M0,388 L0,345 C300,340 580,320 680,150 L680,388 Z" fill="url(#waveFill)"/>
      <path d="M180,325 C380,318 590,292 665,152" fill="none" stroke="#1c2b4a" stroke-width="3" stroke-linecap="round"/>
    </svg>

    <div class="brand">
      <span class="brand__mark"></span>
      <span class="brand__name">VERODEX</span>
    </div>

    <div class="person">
      <p class="person__name"><span class="person__first">DANIEL</span> <span class="person__last">MARLOW</span></p>
      <p class="person__title">Co-Founder</p>
    </div>

    <div class="divider"></div>

    <ul class="contact">
      <li class="contact__item">
        <svg class="contact__icon" viewBox="0 0 16 16" aria-hidden="true"><path d="M4 1 L6.5 4 L5 6 Q6.5 9.5 10 11 L12 9.5 L15 12 L13 15 Q5 14 1 3 Z" fill="#2fa6e0"/></svg>
        555-201-3846
      </li>
      <li class="contact__item">
        <svg class="contact__icon" viewBox="0 0 16 16" aria-hidden="true"><rect x="1" y="3" width="14" height="10" fill="#2fa6e0"/><path d="M1 3 L8 9 L15 3" fill="none" stroke="#fff" stroke-width="1.4"/></svg>
        info@verodex.com
      </li>
      <li class="contact__item">
        <svg class="contact__icon" viewBox="0 0 16 16" aria-hidden="true"><circle cx="8" cy="8" r="7" fill="#2fa6e0"/><ellipse cx="8" cy="8" rx="3" ry="7" fill="none" stroke="#fff" stroke-width="1"/><line x1="1" y1="8" x2="15" y2="8" stroke="#fff" stroke-width="1"/></svg>
        www.verodex.com
      </li>
    </ul>
  </section>
</main>
</body>
</html>
```